Business card for builder specialising in renovations.

Need a card for our building business. Business name is under Martin Powles.
Have licence number on card ( 527691K)
Contact number (0400 382 415)
Want to work on logo for some business cards and shirts - something with MP or MPB or open to ideas??
No animations, No hammers. Something sharp and eye catching.
Highlight that we are a renovation specialist. Simple on front with extra details on back with some lines to jot down things.

Target Market(s)

Renovators

Industry/Entity Type

Building

Contact Information for Business Card

2 sided with room on back to jot things down.
Extra details on back so front can be simple ..like, renovations, bathrooms, decks, extensions, new builds,

Logo Text

MP

Font styles to use
Serif

Requirements
Must have
• Eye catching design .
• Name : Martin powles
• Licence number
• Contact number - 0400382415
Nice to have
• Some logo design that we can carry through to other forms of advertising
• Local builder
• Quality work
Should not have
• No animations

```html
<!DOCTYPE html>
<html lang="en">
<head>
<meta charset="utf-8">
<title>Martin Powles – Business Card</title>
<link rel="stylesheet" href="https://fonts.googleapis.com/css2?family=Open+Sans:wght@400;700;800&display=swap">
<style>
  :root {
    --backdrop: #4e433e;
    --card: #1c1c1d;
    --brand-blue: #3a9ee0;
    --brand-grey: #b4b4b4;
    --note-line: #3c3c3e;
    --white: #ffffff;
  }
  * { box-sizing: border-box; margin: 0; padding: 0; }
  html, body { width: 1200px; height: 716px; overflow: hidden; }
  body {
    background: var(--backdrop);
    font-family: "Open Sans", Arial, sans-serif;
    display: flex;
    align-items: center;
    justify-content: center;
    gap: 90px;
  }
  .card {
    position: relative;
    width: 350px;
    height: 572px;
    background: var(--card);
    border-radius: 4px;
    box-shadow: 0 8px 24px rgba(0,0,0,.35);
    overflow: hidden;
  }
  .brand-name {
    position: absolute;
    left: 0; right: 0;
    top: 92px;
    text-align: center;
    font-weight: 800;
    font-size: 92px;
    line-height: 1;
    letter-spacing: 4px;
    color: var(--brand-grey);
  }
  .services {
    position: absolute;
    top: 262px;
    left: 0; right: 0;
    list-style: none;
    text-align: center;
    color: var(--brand-blue);
    font-size: 21px;
    line-height: 1.38;
  }
  .note-lines {
    position: absolute;
    left: 40px; right: 40px;
    bottom: 40px;
    list-style: none;
  }
  .note-lines li {
    height: 28px;
    border-bottom: 1px solid var(--note-line);
  }
  .owner-name {
    position: absolute;
    top: 262px;
    left: 0; right: 0;
    text-align: center;
    font-weight: 700;
    font-size: 30px;
    letter-spacing: 1px;
    text-transform: uppercase;
  }
  .owner-name__first { color: var(--brand-blue); }
  .owner-name__last { color: var(--brand-grey); }
  .contact-band {
    position: absolute;
    left: 22px; right: 0;
    bottom: 0;
    height: 200px;
    background: var(--brand-blue);
    border-top-left-radius: 22px;
    color: var(--white);
    display: flex;
    flex-direction: column;
    justify-content: center;
    padding-left: 36px;
    gap: 6px;
  }
  .contact-band__phone {
    font-weight: 800;
    font-size: 33px;
    letter-spacing: 1px;
  }
  .contact-band__licence {
    font-size: 22px;
  }
</style>
</head>
<body>
  <section class="card card--details" aria-label="Card side with services">
    <p class="brand-name">MP</p>
    <ul class="services">
      <li>Renovation Specialist</li>
      <li>Bathrooms</li>
      <li>Decks</li>
      <li>Extensions</li>
      <li>New builds,</li>
    </ul>
    <ul class="note-lines" aria-label="Lines for notes">
      <li></li><li></li><li></li>
    </ul>
  </section>

  <section class="card card--contact" aria-label="Card side with contact details">
    <p class="brand-name">MP</p>
    <p class="owner-name">
      <span class="owner-name__first">Martin</span>
      <span class="owner-name__last">Powles</span>
    </p>
    <div class="contact-band">
      <p class="contact-band__phone">0400 382 415</p>
      <p class="contact-band__licence">Licence number 527691K</p>
    </div>
  </section>
</body>
</html>
```